Dynamic Business Card for Sports Supplements Company

Hi! I'm looking for an awesome business card to match my existing sports supplement company. I have uploaded my current company logo and screenshot of the front page of my website.

I would like to have something dynamic and interesting and utilize the colors in the website - the reds and purples

The business card should be double sided and focus on a unique eye-catching design on the back and include all the relevant company info.

Most importantly, it should say somewhere: "Sign up on our website for a coupon code."

Target Market(s)

Mostly for women gym goers but it shouldn't be too feminine. It should be in keeping with the website design. It should flow and clearly be connected to it

Industry/Entity Type

Business

Contact Information for Business Card

Lorraine K. Vestal
CEO
LVestal@Quorvanexco.com
www.quorvanexco.com
555.417.3820
P.O. Box 47315
Halverton, Ostmere 00000

Sign up on our website for a coupon code

Font styles to use
Serif
Sans Serif
Other font styles liked:
• Novecento font family and "Quorvanex" is in AR Destine font

Requirements
Must have
• One side should be a bold Quorvanex logo design. Even just the symbol itself may be o.k. (see attached file)

```html
<!DOCTYPE html>
<html lang="en">
<head>
<meta charset="utf-8">
<title>Quorvanex Business Card</title>
<link rel="stylesheet" href="https://fonts.googleapis.com/css2?family=Roboto+Condensed:wght@400;700&display=swap">
<style>
  :root {
    --bg: #e9e6e1;
    --card-black: #111111;
    --card-black-hi: #262626;
    --brand-red: #e3202c;
    --brand-red-hi: #f0404a;
    --white: #ffffff;
    --muted: #d8d8d8;
  }
  * { margin: 0; padding: 0; box-sizing: border-box; }
  html, body {
    width: 1200px; height: 950px; overflow: hidden;
    background: var(--bg);
    font-family: "Roboto Condensed", "Arial Narrow", sans-serif;
  }
  .sheet {
    width: 1200px; height: 950px;
    display: flex; flex-direction: column; align-items: center; justify-content: center; gap: 50px;
  }
  .card {
    position: relative; width: 700px; height: 400px; overflow: hidden;
    box-shadow: 0 10px 24px rgba(0,0,0,.22);
  }

  /* Front: contact side */
  .card--front { background: linear-gradient(135deg, var(--card-black-hi) 0%, var(--card-black) 55%); color: var(--white); }
  .name-band {
    position: absolute; top: 40px; right: 0; width: 330px; height: 74px;
    background: var(--brand-red);
    clip-path: polygon(40px 0, 100% 0, 100% 100%, 0 100%);
    display: flex; align-items: center; justify-content: flex-end; gap: 10px; padding-right: 30px;
  }
  .name-band .name { font-weight: 700; font-size: 27px; letter-spacing: .3px; }
  .name-band .title { font-size: 16px; align-self: flex-end; margin-bottom: 24px; }

  .brand { display: flex; align-items: center; gap: 10px; }
  .brand-mark { width: 16px; height: 16px; background: var(--brand-red); flex: none; }
  .brand-name { font-weight: 700; text-transform: uppercase; letter-spacing: 1px; }
  .brand-tagline { text-transform: uppercase; letter-spacing: 2.6px; font-size: 11px; }

  .card--front .brand-block { position: absolute; left: 52px; top: 150px; }
  .card--front .brand-name { font-size: 38px; color: var(--white); }
  .card--front .brand-tagline { color: var(--muted); margin: 4px 0 0 26px; }

  .contact { position: absolute; left: 78px; top: 252px; font-size: 16px; line-height: 24px; list-style: none; }
  .contact li { display: flex; align-items: center; gap: 10px; }
  .contact .address { margin-bottom: 4px; padding-left: 26px; }
  .contact svg { width: 16px; height: 16px; flex: none; }

  /* Back: brand side */
  .card--back { background: linear-gradient(120deg, var(--brand-red) 0%, var(--brand-red-hi) 60%, var(--brand-red) 100%); color: var(--white); }
  .card--back .brand-block { position: absolute; left: 0; right: 0; top: 128px; display: flex; flex-direction: column; align-items: center; }
  .card--back .brand-mark { width: 26px; height: 26px; background: var(--white); }
  .card--back .brand-name { font-size: 62px; color: var(--white); letter-spacing: 2px; }
  .card--back .brand-tagline { font-size: 14px; letter-spacing: 4px; margin-top: 4px; }
  .promo { position: absolute; left: 0; right: 0; bottom: 48px; text-align: center; font-size: 19px; letter-spacing: .4px; }
</style>
</head>
<body>
<main class="sheet">

  <section class="card card--front" aria-label="Business card front">
    <div class="name-band">
      <span class="name">Lorraine K. Vestal</span>
      <span class="title">CEO</span>
    </div>

    <div class="brand-block">
      <div class="brand">
        <span class="brand-mark"></span>
        <span class="brand-name">Quorvanex</span>
      </div>
      <p class="brand-tagline">Your Strength Companion</p>
    </div>

    <ul class="contact">
      <li class="address">P.O. Box 47315<br>Halverton, Ostmere 00000</li>
      <li>
        <svg viewBox="0 0 16 16" aria-hidden="true"><rect width="16" height="16" rx="3" fill="var(--brand-red)"/><path d="M5 3.5l1.6 2.3-1 1c.6 1.4 1.5 2.3 2.9 2.9l1-1 2.3 1.6-.8 1.9C7.5 12 4 8.5 3.6 4.3z" fill="#fff"/></svg>
        <span>555.417.3820</span>
      </li>
      <li>
        <svg viewBox="0 0 16 16" aria-hidden="true"><rect width="16" height="16" rx="3" fill="var(--brand-red)"/><rect x="3.5" y="5" width="9" height="6.5" fill="none" stroke="#fff" stroke-width="1.2"/><path d="M3.5 5l4.5 3.6L12.5 5" fill="none" stroke="#fff" stroke-width="1.2"/></svg>
        <span>LVestal@Quorvanexco.com</span>
      </li>
      <li>
        <svg viewBox="0 0 16 16" aria-hidden="true"><circle cx="8" cy="8" r="8" fill="var(--brand-red)"/><circle cx="8" cy="8" r="4.5" fill="none" stroke="#fff" stroke-width="1.1"/><path d="M3.5 8h9M8 3.5c-2 2.5-2 6.5 0 9M8 3.5c2 2.5 2 6.5 0 9" fill="none" stroke="#fff" stroke-width="1"/></svg>
        <span>www.quorvanexco.com</span>
      </li>
    </ul>
  </section>

  <section class="card card--back" aria-label="Business card back">
    <div class="brand-block">
      <div class="brand">
        <span class="brand-mark"></span>
        <span class="brand-name">Quorvanex</span>
      </div>
      <p class="brand-tagline">Your Strength Companion</p>
    </div>
    <p class="promo">Sign up on our website for a coupon code</p>
  </section>

</main>
</body>
</html>
```